Bold, Modern, Clean "Kestrelwaymassage.com" website

Why we stand out?
We are a male and female mobile massage team. Our names are Paul and Lina. 
Kestrel Way is a Seattle based mobile massage service. Our massage is offered to the community with a goal of facilitating balance within each individual. We specialize in integrated Pain management, and sports/medical massage therapy. Every client's first assessment is attended by our male and female massage therapist team. Depending on the goals identified for an individual determines which therapist will be assigned to provide treatment, if not both.

Our passion...
Here at Kestrel Way, we have a great passion for Postural Resoration and how it is integrated into an individual's Massage treatment. We pride ourselves in being natural facilitators of healing, which takes the ego of the therapist out of the client's healing process. We strive to deliver the best massage possible by including modalities such as Neuromuscular, Myofascial release, spontaneous muscle release, postural restoration, orthopedic, and medical massage.

Our education...

We are both Graduates of Venmora, school of massage therapy. We have continuing education in medical massage, myofacial release, trigger point therapy, postural restoration, anatomy, and spontaneous muscle release. Lina is also a Certified Yoga Instructor, which amplifies her experience with flexibility and strength as it pertains to each individual. Paul's passion is Massage, stretching, and strength training to encourage postural restoration and realignment.

Our rates-

Our rates are $75/ 60 minutes, $95/ 90 minutes, and $120/ 120 minutes.

Education-
Both Lina and I worked as behavioral health professionals that specialized in life skills mentoring for youth who had experienced different types of trauma. This led us both to want to help others in a different environment, where individuals can be empowered to take responsibility over their own healing. To us, massage is a type of manipulation physical therapy, that encourages healing on many levels.

Advice to any massage client-
The most important thing to 'us', as Licenced providers is to get you on to our table to show you our skills. But a good therapist never forgets that it's not about what we do for you, but what we can facilitate for you. Your health and healing has nothing to do with us. It is yours, not ours. Identify what your goals are with any Therapist, and know what the end looks like. Progress should be tangible, such as range of motion, and decreased pain.

Lina and Paul at Kestrel Way are awesome! I recently had open heart surgery, and Lina worked on me to increase my range of motion while helping with the pinched nerve from my arm being in the same position for so long during my surgery. My wife drives a lot for work, and Paul has helped decrease her neck and lower back pain immensely. They are seriously the best therapists I have ever worked with. I would recommend them to anyone who needs anything from stress relief to a medical massage treatment. They are professional, up beat, easy going, and always on time. And, I love that they meet us where ever we like! We did a staycation recently, where they came to our hotel to give us relaxation massages. Although usually they come to our home, where we focus on pain related issues. We will continue to work with them for a long, long time.

Target Market(s)

Mobile massage therapy clients

Industry/Entity Type

Massage Therapy

Coding

Coded - Design and coding required

Number of Pages Required

1 page

Font styles to use
Serif
Sans Serif

Requirements
Must have
• Please add or remove any information that would help the presentation of our website. Our logo is posted below, please include into the website.
• Please include a contact field that includes, kestrelwaymassage@fernmail.net,
• (206) 555-0148
• We have also included our own stock photos, as well as a photo of Paul and Lina. Please include a cropped photo of both massage therapists.

```html
<!DOCTYPE html>
<html lang="en">
<head>
<meta charset="utf-8">
<title>Kestrel Way – Mobile Massage</title>
<link href="https://fonts.googleapis.com/css2?family=Open+Sans:ital,wght@0,400;0,600;0,700;0,800;1,400&family=Cinzel:wght@400&family=Playfair+Display:ital@1&display=swap" rel="stylesheet">
<style>
:root{
  --blue:#1b35a3;
  --blue-light:#2446c2;
  --green:#13916f;
  --green-dark:#0f7a5d;
  --ink:#333;
  --muted:#666;
  --band:#ececec;
  --footer:#e8e8e8;
  --white:#fff;
}
*{box-sizing:border-box;margin:0;padding:0}
html,body{width:743px;height:1200px;overflow:hidden;background:var(--white)}
body{position:relative;font-family:"Open Sans",Arial,sans-serif;color:var(--ink)}
.abs{position:absolute}

/* header */
.brand-badge{left:62px;top:5px;width:79px;height:79px;border-radius:50%;background:var(--blue);border:3px solid var(--blue-light);display:flex;align-items:center;justify-content:center;color:var(--white);font-weight:700;font-size:13px;text-align:center;line-height:1.1}
.quick-contact{left:328px;top:36px;display:flex;align-items:center;gap:7px;font-size:8px;color:#555}
.quick-contact .icon{width:22px;height:22px;border-radius:50%;background:var(--green);display:flex;align-items:center;justify-content:center}
.quick-contact b{color:var(--blue);font-weight:600}
.btn-head{top:37px;height:23px;background:var(--green);color:var(--white);font-size:7px;font-weight:700;display:flex;align-items:center;justify-content:space-between;padding:0 10px;letter-spacing:.2px}
.btn-head.login{left:485px;width:95px}
.btn-head.subscribe{left:587px;width:95px}

/* nav */
.nav{left:0;top:86px;width:743px;height:24px;background:linear-gradient(#2447c4,#1b36a6)}
.nav ul{list-style:none;position:absolute;left:62px;top:0;display:flex}
.nav li{width:88.6px;height:24px;line-height:24px;padding-left:11px;font-size:6.5px;color:var(--white);border-right:1px solid rgba(255,255,255,.15)}
.nav li.active{background:var(--green)}

/* hero */
.hero{left:0;top:110px;width:743px;height:313px;background:radial-gradient(ellipse at 30% 40%,#9a7866 0%,#5e4538 55%,#3a2a22 100%)}
.hero-overlay{left:0;top:110px;width:743px;height:313px;background:rgba(40,28,22,.35)}
.therapist{top:172px;width:60px;height:60px;border-radius:50%;border:3px solid rgba(255,255,255,.6);background:linear-gradient(#c9a68c,#8b6a55)}
.hero-title{left:0;width:743px;top:238px;text-align:center;font-family:"Cinzel",serif;color:#2fb58c;font-size:21px;letter-spacing:1px}
.hero-text{left:0;width:743px;top:272px;text-align:center;color:var(--white);font-size:10px;line-height:19px}
.hero-text b{color:#2fc08f;font-size:12px;font-weight:600}
.stars{left:0;width:743px;top:314px;text-align:center;color:#f5c518;font-size:11px;letter-spacing:1px}
.review{left:0;width:743px;top:333px;text-align:center;color:var(--white);font-size:9.5px}
.review i{font-size:6.5px}
.dots{left:354px;top:396px;display:flex;gap:4px}
.dots span{width:5px;height:5px;border-radius:50%;background:rgba(255,255,255,.4)}
.dots span:first-child{background:var(--white)}
.side-tab{left:714px;top:165px;width:29px;height:112px;background:var(--blue);color:var(--white)}
.side-tab .label{position:absolute;left:7px;top:100px;transform:rotate(-90deg);transform-origin:left top;font-size:7.5px;font-weight:700;white-space:nowrap}

/* features */
.feature-img{top:446px;width:202px;height:195px}
.feature-img .notch{position:absolute;left:87px;bottom:0;width:0;height:0;border-left:14px solid transparent;border-right:14px solid transparent;border-bottom:14px solid var(--white)}
.feature{top:658px;width:202px;text-align:center}
.feature .kicker{font-size:10px;font-weight:700;letter-spacing:1.2px;color:#222}
.feature h2{font-size:19px;font-weight:800;color:var(--blue);margin-top:2px}
.feature p{font-size:6.6px;line-height:15px;color:var(--muted);margin-top:8px;padding:0 4px}
.btn-detail{top:775px;width:120px;height:25px;background:var(--green);color:var(--white);font-size:7px;font-weight:700;letter-spacing:2px;display:flex;align-items:center;justify-content:center;gap:12px;box-shadow:0 5px 5px -3px rgba(0,0,0,.3)}

/* rates */
.rates-title{left:76px;top:867px;font-family:"Playfair Display",serif;font-style:italic;color:var(--blue);font-size:20px}
.rates-text{left:78px;top:895px;width:230px;font-size:6.8px;line-height:15px;color:var(--muted)}
.rate{top:845px;width:90px;height:90px;border-radius:50%;color:var(--white);text-align:center;padding-top:22px}
.rate b{display:block;font-size:27px;font-weight:700;line-height:1}
.rate span{display:block;font-size:7px;margin-top:8px}
.rate.green{background:var(--green)}
.rate.blue{background:var(--blue)}
.rate-shadow{top:941px;width:50px;height:5px;border-radius:50%;background:rgba(0,0,0,.15);filter:blur(2px)}

/* newsletter */
.newsletter{left:0;top:982px;width:743px;height:51px;background:var(--band);border-top:1px solid #ddd;border-bottom:1px solid #ddd}
.newsletter .label{position:absolute;left:62px;top:18px;font-size:8px;color:#444}
.newsletter .label b{font-size:10.5px;font-weight:700;color:#222;margin-right:3px}
.newsletter .field{position:absolute;left:361px;top:15px;width:194px;height:20px;background:var(--white);border:1px solid #ccc;font-size:5px;color:#999;padding:6px 9px}
.newsletter .send{position:absolute;left:561px;top:15px;width:121px;height:20px;background:var(--green);color:var(--white);font-size:7px;letter-spacing:2px;font-weight:600;text-align:center;line-height:20px}

/* footer */
.footer{left:0;top:1033px;width:743px;height:127px;background:var(--footer)}
.foot-col{top:1051px}
.foot-col h3{font-size:8.5px;font-weight:700;color:#222;line-height:12px}
.foot-col h3 em{font-style:normal;color:var(--green);display:block}
.foot-col ul{list-style:none;margin-top:7px}
.foot-col li{font-size:6.5px;color:#555;line-height:14.8px}
.socials{left:435px;top:1087px;display:flex;gap:6px}
.socials span{width:17px;height:17px;border-radius:50%;background:#8a8a8a}
.foot-badge{left:592px;top:1051px;width:76px;height:76px;border-radius:50%;background:var(--blue);border:3px solid var(--blue-light);display:flex;align-items:center;justify-content:center;color:var(--white);font-weight:700;font-size:12px;text-align:center;line-height:1.1}
.copyright{left:0;width:743px;top:1176px;text-align:center;font-size:6.5px;color:#555}
</style>
</head>
<body>

<header>
  <div class="abs brand-badge">Kestrel<br>Way</div>
  <div class="abs quick-contact">
    <span class="icon"><svg width="10" height="10" viewBox="0 0 24 24"><path fill="#fff" d="M6.6 10.8a15 15 0 0 0 6.6 6.6l2.2-2.2a1 1 0 0 1 1-.25 11.4 11.4 0 0 0 3.6.57 1 1 0 0 1 1 1V20a1 1 0 0 1-1 1A17 17 0 0 1 3 4a1 1 0 0 1 1-1h3.5a1 1 0 0 1 1 1c0 1.25.2 2.45.57 3.57a1 1 0 0 1-.25 1z"/></svg></span>
    Quick contact - <b>(206) 555-0148</b>
  </div>
  <div class="abs btn-head login">MEMBERS LOGIN <span>&#8964;</span></div>
  <div class="abs btn-head subscribe">SUBSCRIBE HERE <span>&#8964;</span></div>
</header>

<nav class="abs nav">
  <ul>
    <li class="active">HOME</li><li>ABOUT US</li><li>SERVICES</li><li>WHY WE STAND OUT?</li><li>OUR PASSION</li><li>OUR EDUCATION</li><li>CONTACT US</li>
  </ul>
</nav>

<section>
  <div class="abs hero" role="img" aria-label="Woman relaxing during a back massage"></div>
  <div class="abs hero-overlay"></div>
  <div class="abs therapist" style="left:306px" role="img" aria-label="Portrait of therapist Lina"></div>
  <div class="abs therapist" style="left:376px" role="img" aria-label="Portrait of therapist Paul"></div>
  <h1 class="abs hero-title">MASSAGE THERAPY</h1>
  <p class="abs hero-text">We are a male and female mobile massage team. Our names are <b>Paul</b> and <b>Lina</b>.<br>Kestrel Way is a Seattle based mobile massage service.</p>
  <div class="abs stars">★★★★★</div>
  <p class="abs review">Stars Massage Therapy, <i>Verified Review</i></p>
  <div class="abs dots"><span></span><span></span><span></span><span></span></div>
  <div class="abs side-tab">
    <svg class="abs" style="left:7px;top:9px" width="15" height="15" viewBox="0 0 16 16"><circle cx="8" cy="8" r="6.5" fill="none" stroke="#fff" stroke-width="1.4"/><path d="M9.3 5 6.3 8l3 3" fill="none" stroke="#fff" stroke-width="1.4"/></svg>
    <span class="label">QUICK CONTACT</span>
  </div>
</section>

<section>
  <div class="abs feature-img" style="left:62px;background:linear-gradient(135deg,#6b4a3a,#e7cfc0 55%,#f2ece8)" role="img" aria-label="Woman receiving a facial massage"><span class="notch"></span></div>
  <div class="abs feature-img" style="left:271px;background:linear-gradient(135deg,#d8cbb6,#b89a80 55%,#5a4636)" role="img" aria-label="Hot stone massage on a woman's back"><span class="notch"></span></div>
  <div class="abs feature-img" style="left:481px;background:linear-gradient(135deg,#5a2a18,#a86a46 45%,#e8e2da 70%,#6a3a22)" role="img" aria-label="Herbal compress balls, towel and candle"><span class="notch"></span></div>

  <div class="abs feature" style="left:62px"><div class="kicker">WHY WE</div><h2>STAND OUT?</h2><p>We are a male and female mobile massage team. Our names are Paul and Lina. Kestrel Way is a Seattle based mobile massage service. Our massage is offered to the community with a goal of facilitating...</p></div>
  <div class="abs feature" style="left:271px"><div class="kicker">OUR</div><h2>PASSION</h2><p>Here at Kestrel Way, we have a great passion for Postural Resoration and how it is integrated into an individual's Massage treatment. We pride ourselves in being natural facilitators of healing...</p></div>
  <div class="abs feature" style="left:481px"><div class="kicker">OUR</div><h2>EDUCATION</h2><p>We are both Graduates of Venmora, school of massage therapy. We have continuing education in medical massage, myofacial release, trigger point therapy, postural restoration, anatomy...</p></div>

  <div class="abs btn-detail" style="left:103px">VIEW DETAILS <span>»</span></div>
  <div class="abs btn-detail" style="left:312px">VIEW DETAILS <span>»</span></div>
  <div class="abs btn-detail" style="left:522px">VIEW DETAILS <span>»</span></div>
</section>

<section>
  <h2 class="abs rates-title">Our rates are</h2>
  <p class="abs rates-text">Lorem Ipsum is simply dummy text of the printing and typesetting industry. Lorem Ipsum has been the industry...</p>
  <div class="abs rate green" style="left:325px"><b>$75</b><span>60 MINUTES</span></div>
  <div class="abs rate blue" style="left:442px"><b>$95</b><span>90 MINUTES</span></div>
  <div class="abs rate blue" style="left:559px"><b>$120</b><span>120MINUTES</span></div>
  <div class="abs rate-shadow" style="left:345px"></div>
  <div class="abs rate-shadow" style="left:462px"></div>
  <div class="abs rate-shadow" style="left:579px"></div>
</section>

<section class="abs newsletter">
  <div class="label"><b>NEWSLETTER SIGNUP</b> Get our recent updates through your email id :</div>
  <div class="field">ENTER YOUR EMAIL ID :</div>
  <div class="send">SUBSCRIBE NOW</div>
</section>

<footer>
  <div class="abs footer"></div>
  <div class="abs foot-col" style="left:62px"><h3>ABOUT<em>KESTREL WAY</em></h3><ul><li>Why we stand out?</li><li>Our passion.</li><li>Our education.</li><li>Our rates</li></ul></div>
  <div class="abs foot-col" style="left:184px"><h3>CUSTOMER<em>SERVICE</em></h3><ul><li>Home Service</li><li>Refunds and returns</li><li>24 hours support</li><li>Gift Box</li></ul></div>
  <div class="abs foot-col" style="left:312px"><h3>KESTREL WAY<em>INFORMATION</em></h3><ul><li>Terms &amp; Conditions</li><li>Privacy Policy</li><li>Disclaimer</li><li>Sitemap</li></ul></div>
  <div class="abs foot-col" style="left:434px"><h3>CONNECT WITH OUR<em>SOCIAL NETWORK</em></h3></div>
  <div class="abs socials"><span></span><span></span><span></span><span></span><span></span></div>
  <div class="abs foot-badge">Kestrel<br>Way</div>
  <p class="abs copyright">© 2015. Kestrel Way. All rights reserved.</p>
</footer>

</body>
</html>
```